Business software developers new website

We need to redesign our website. Our current website is http://www.plovencast.example/index.html, which is outdated and needs a new look. We moved out from web design and have concentrated more on the back end of the systems, for example, system support and security and cloud-based applications. Our major clients include both private and government sectors. We would like to see some designs that are all in one page, simple and clean. Prefer illustrator or obstructed images instead of real-life photos. Must look futuristic yet friendly. Attached the new logo for your references and good luck.

Target Market(s)

Medium to big company for their IT or data management. Either improve or upgrade their current system.

Industry/Entity Type

Business Software

Number of Pages Required

1 page

Colors

Designer to choose colors to be used in the design.

Requirements
Must have
• Simple and clean. Individual assets must be provided in the correct size and format(png or jpeg). Prefer Goggle fonts. Even though the logo color is red, grey and black, still prefer some modern colors that go well with red. When design, must consider the possibility to convert it into responsive.
Nice to have
• White background
Should not have
• real life photos, no slider

```html
<!DOCTYPE html>
<html lang="en">
<head>
<meta charset="utf-8">
<title>Plovencast</title>
<link href="https://fonts.googleapis.com/css2?family=Fira+Sans+Condensed:wght@300;400;500&family=Montserrat:wght@400;500;600&display=swap" rel="stylesheet">
<style>
:root{
  --red:#e1001a;
  --red-deep:#c20016;
  --ink:#1d1d24;
  --navy:#2f2e41;
  --grey:#f2f2f3;
  --grey-mid:#e7e7e9;
  --text:#3a3a44;
  --pink:#fde3e6;
  --white:#ffffff;
}
*{box-sizing:border-box;margin:0;padding:0}
html,body{width:1200px;height:3559px;overflow:hidden;background:var(--white)}
body{font-family:"Fira Sans Condensed",sans-serif;color:var(--ink)}
.page{position:relative;width:1200px;height:3559px;overflow:hidden}
.abs{position:absolute}
.backdrop{position:absolute;left:0;top:0}
.brand{font-family:"Fira Sans Condensed",sans-serif;font-weight:400;color:var(--white);font-size:40px;letter-spacing:.5px}
.nav{display:flex;gap:0;top:52px;font-size:18px;color:var(--white);list-style:none}
.nav li{position:absolute;white-space:nowrap}
.nav .dark{color:var(--ink)}
.hero-title{left:90px;top:170px;font-size:62px;font-weight:400;color:var(--white)}
.hero-text{left:90px;top:250px;width:490px;font-size:21px;line-height:29px;font-weight:300;color:var(--white)}
.btn-outline{left:90px;top:379px;width:171px;height:53px;border:2px solid var(--white);border-radius:3px;color:var(--white);font-family:"Montserrat",sans-serif;font-size:17px;display:flex;align-items:center;justify-content:center}
.illus{border-radius:20px}
.section-title{font-size:45px;font-weight:400;color:var(--ink)}
.center{left:0;width:1200px;text-align:center}
.service{width:320px;height:110px}
.service .icon{position:absolute;left:0;top:0;width:75px;height:75px;border-radius:50%;background:var(--pink);display:flex;align-items:center;justify-content:center}
.service h3{position:absolute;left:89px;top:-4px;font-family:"Montserrat",sans-serif;font-weight:500;font-size:18px;color:var(--ink)}
.service p{position:absolute;left:89px;top:26px;width:200px;font-size:14px;line-height:21.5px;font-weight:300;color:var(--ink)}
.clients-text{left:471px;top:1384px;width:630px;font-size:14.5px;line-height:27px;font-weight:300;color:var(--text)}
.client-card{top:1527px;width:205px;height:105px;background:var(--white);border-radius:10px;box-shadow:0 4px 14px rgba(0,0,0,.09);display:flex;align-items:center;justify-content:center;gap:8px;font-family:"Fira Sans Condensed",sans-serif;font-size:22px;font-weight:500;color:var(--navy)}
.client-card .mark{width:14px;height:14px;background:var(--red);border-radius:50%}
.about-text{left:145px;top:1887px;width:910px;text-align:center;font-size:16.5px;line-height:29px;font-weight:300;color:var(--ink)}
.faq-card{left:90px;width:507px;background:var(--white);border-radius:12px;box-shadow:0 4px 16px rgba(0,0,0,.08)}
.faq-q{position:absolute;left:21px;font-family:"Montserrat",sans-serif;font-weight:500;font-size:17px;color:var(--ink)}
.faq-qtext{position:absolute;left:60px;width:420px;font-family:"Montserrat",sans-serif;font-weight:500;font-size:16px;line-height:25px;color:var(--ink)}
.faq-a{position:absolute;left:58px;top:86px;width:440px;font-size:13.5px;line-height:23.5px;font-weight:300;color:var(--text)}
.field{background:var(--white);border:1px solid #d6d6da;font-family:"Montserrat",sans-serif;font-size:13.5px;color:#555;padding:16px 22px}
.btn-red{left:518px;top:2972px;width:164px;height:47px;background:var(--red);color:var(--white);border-radius:3px;font-family:"Montserrat",sans-serif;font-size:16px;display:flex;align-items:center;justify-content:center}
.contact-band{left:0;top:3135px;width:1200px;height:145px;background:var(--red)}
.contact-item{top:3183px;display:flex;align-items:center;gap:12px;color:var(--white);font-family:"Montserrat",sans-serif;font-size:14.5px;line-height:22px}
.contact-item .dot{width:46px;height:46px;border-radius:50%;background:var(--navy);display:flex;align-items:center;justify-content:center;flex:none}
.footer{left:0;top:3280px;width:1200px;height:279px;background:linear-gradient(135deg,var(--red-deep),var(--red) 60%,#d40019)}
.social{top:3384px;width:51px;height:51px;border:2px solid var(--white);border-radius:50%;color:var(--white);font-family:"Montserrat",sans-serif;font-size:10px;display:flex;align-items:center;justify-content:center}
.footer-links{top:3474px;color:var(--white);font-family:"Montserrat",sans-serif;font-size:13.5px;word-spacing:0}
.footer-links span{margin:0 20px}
.copyright{top:3510px;color:var(--white);font-family:"Montserrat",sans-serif;font-size:13px}
</style>
</head>
<body>
<div class="page">

  <svg class="backdrop" width="1200" height="3559" viewBox="0 0 1200 3559" aria-hidden="true">
    <defs>
      <linearGradient id="heroRed" x1="0" y1="0" x2="1" y2="1">
        <stop offset="0" stop-color="#c50017"/>
        <stop offset=".5" stop-color="#e1001a"/>
        <stop offset="1" stop-color="#d60019"/>
      </linearGradient>
    </defs>
    <path d="M0 0 H775 C690 40 640 140 630 250 C620 360 590 520 420 555 C300 580 160 560 0 568 Z" fill="url(#heroRed)"/>
    <circle cx="828" cy="130" r="30" fill="#f1f1f2"/>
    <path d="M1200 40 C1130 40 1110 110 1115 140 C1120 185 1160 190 1200 188 Z" fill="#f1f1f2"/>
    <path d="M0 1560 C80 1360 300 1250 600 1255 C820 1260 1000 1250 1200 1195 V2120 H0 Z" fill="#f3f3f4"/>
    <path d="M0 2110 H1200 V3135 H0 Z" fill="#f3f3f4"/>
    <path d="M0 2110 C200 2100 380 2130 520 2300 C650 2460 690 2700 820 2880 C900 2990 1020 3060 1200 3080 V3135 H0 Z" fill="#efeff0"/>
    <path d="M700 2700 C820 2960 1000 3090 1200 3100 V3135 H640 Z" fill="#ffffff" opacity=".6"/>
  </svg>

  <div class="abs brand" style="left:90px;top:40px">plovencast</div>
  <ul class="abs nav">
    <li style="left:600px">Home</li>
    <li class="dark" style="left:722px">Our Services</li>
    <li class="dark" style="left:893px">Our Clients</li>
    <li class="dark" style="left:1052px">Contact</li>
  </ul>

  <h1 class="abs hero-title">Plovencast</h1>
  <p class="abs hero-text">We have provided web design, graphic design and application development solutions for a wide variety of industries</p>
  <div class="abs btn-outline">CONTACT US</div>

  <div class="abs illus" role="img" aria-label="Illustration of two people seated at a desk working on a computer, beside a potted plant" style="left:655px;top:195px;width:510px;height:350px;background:linear-gradient(135deg,#f4f4f6,#e9e9ee 60%,#f7d6da)"></div>

  <h2 class="abs section-title center" style="top:725px">Works &amp; Technology</h2>

  <div class="abs service" style="left:90px;top:838px">
    <div class="icon"><svg width="36" height="36" viewBox="0 0 36 36" fill="none" stroke="#e1001a" stroke-width="1.8"><rect x="5" y="5" width="26" height="26" rx="2"/><line x1="5" y1="11" x2="31" y2="11"/><rect x="9" y="15" width="8" height="12"/><line x1="20" y1="16" x2="27" y2="16"/><line x1="20" y1="21" x2="27" y2="21"/></svg></div>
    <h3>Web Design</h3>
    <p>Your website needs the 'wow' factor to meet you're audiences needs...</p>
  </div>
  <div class="abs service" style="left:464px;top:838px">
    <div class="icon"><svg width="36" height="36" viewBox="0 0 36 36" fill="none" stroke="#e1001a" stroke-width="1.8"><rect x="4" y="6" width="28" height="19" rx="2"/><line x1="14" y1="30" x2="22" y2="30"/><line x1="18" y1="25" x2="18" y2="30"/><circle cx="24" cy="15" r="4"/><line x1="8" y1="12" x2="16" y2="12"/><line x1="8" y1="17" x2="16" y2="17"/></svg></div>
    <h3>Software Development</h3>
    <p>We build robust, reliable websites – and make sure they stay that way. We cover all...</p>
  </div>
  <div class="abs service" style="left:838px;top:838px">
    <div class="icon"><svg width="36" height="36" viewBox="0 0 36 36" fill="none" stroke="#e1001a" stroke-width="1.8"><path d="M6 14 L20 8 V26 L6 20 Z"/><rect x="20" y="12" width="5" height="10"/><path d="M9 21 L11 30 H15 L13 22"/><line x1="28" y1="17" x2="32" y2="17"/></svg></div>
    <h3>Marketing</h3>
    <p>Beside using the latest techniques to improve your Search Engine Ranking ...</p>
  </div>
  <div class="abs service" style="left:90px;top:990px">
    <div class="icon"><svg width="36" height="36" viewBox="0 0 36 36" fill="none" stroke="#e1001a" stroke-width="1.8"><rect x="4" y="6" width="28" height="19" rx="2"/><line x1="14" y1="30" x2="22" y2="30"/><path d="M14 12 L10 15.5 L14 19"/><path d="M22 12 L26 15.5 L22 19"/><line x1="19" y1="11" x2="17" y2="20"/></svg></div>
    <h3>Programming</h3>
    <p>We specialize in a variety of programming languages, but primarily use...</p>
  </div>
  <div class="abs service" style="left:464px;top:990px">
    <div class="icon"><svg width="36" height="36" viewBox="0 0 36 36" fill="none" stroke="#e1001a" stroke-width="1.8"><circle cx="18" cy="18" r="8"/><circle cx="18" cy="18" r="13" stroke-dasharray="4 3"/><path d="M18 13 L22 21 H14 Z"/></svg></div>
    <h3>Wc3 Compliant</h3>
    <p>All of our sites are W3C compliant, so you never have to worry ...</p>
  </div>
  <div class="abs service" style="left:838px;top:990px">
    <div class="icon"><svg width="36" height="36" viewBox="0 0 36 36" fill="none" stroke="#e1001a" stroke-width="1.8"><rect x="5" y="6" width="22" height="8" rx="1"/><rect x="5" y="16" width="22" height="8" rx="1"/><rect x="5" y="26" width="14" height="6" rx="1"/><circle cx="27" cy="28" r="5"/><circle cx="27" cy="28" r="2"/></svg></div>
    <h3>Hosting Solutions</h3>
    <p>We offer competitive hosting solutions with all of our projects so you never...</p>
  </div>

  <h2 class="abs section-title" style="left:470px;top:1312px">Our Clients</h2>
  <p class="abs clients-text">We undertake many projects from small businesses to large corporations. We are also extremely experienced in the long term support of comprehensive web based business systems providing first class development, maintenance, data entry services and enhancements.</p>
  <div class="abs illus" role="img" aria-label="Illustration of a person sitting cross-legged with a laptop between plants" style="left:12px;top:1415px;width:433px;height:235px;background:linear-gradient(160deg,#f3f3f4,#e6e6ea 55%,#f5cfd4)"></div>

  <div class="abs client-card" style="left:471px"><span class="mark"></span>Brightmill</div>
  <div class="abs client-card" style="left:688px"><span class="mark" style="border-radius:2px;background:var(--navy)"></span>Corvale Health</div>
  <div class="abs client-card" style="left:904px">Marenti's</div>

  <h2 class="abs section-title center" style="top:1813px">About Us</h2>
  <p class="abs about-text">We have provided web design, graphic design and application development solutions for a wide variety of industries. We are known for the quality of our work, affordable rates and our individual approach to each customer. Our company offers a wide variety of professional web solution and all this at very competitive prices!</p>

  <h2 class="abs section-title" style="left:88px;top:2165px">Faq</h2>
  <div class="abs faq-card" style="top:2243px;height:202px">
    <span class="faq-q" style="top:21px">Q)</span>
    <p class="faq-qtext" style="top:22px">How much does a web site powered by Plovencast cost?</p>
    <p class="faq-a">There are quite a few factors that are going to affect the ultimate cost of your web site. These factors include how many pages you are going to have, if you will sell products on your website, the graphic work involved, and how interactive your web site will be.</p>
  </div>
  <div class="abs faq-card" style="top:2460px;height:80px">
    <span class="faq-q" style="top:27px">Q)</span>
    <p class="faq-qtext" style="top:27px">How long does it take to have a web site designed?</p>
  </div>
  <div class="abs illus" role="img" aria-label="Illustration of a person standing beside chat message bubbles and a plant" style="left:690px;top:2228px;width:475px;height:320px;background:linear-gradient(150deg,#e8e8ec,#d9d9df 55%,#f4d0d5)"></div>

  <h2 class="abs section-title center" style="top:2708px">Quick Contact</h2>
  <div class="abs field" style="left:189px;top:2797px;width:401px;height:45px;padding-top:13px">Your Name</div>
  <div class="abs field" style="left:610px;top:2797px;width:401px;height:45px;padding-top:13px">Where I can reply?</div>
  <div class="abs field" style="left:189px;top:2862px;width:822px;height:90px">Talk to me</div>
  <div class="abs btn-red">SEND MESSAGE</div>
  <div class="abs illus" role="img" aria-label="Illustration of a person seated with a laptop next to a small plant" style="left:8px;top:2905px;width:254px;height:245px;background:linear-gradient(160deg,#efeff1,#e4e4e8 55%,#f6cdd2)"></div>

  <div class="abs contact-band"></div>
  <div class="abs contact-item" style="left:90px">
    <span class="dot"><svg width="18" height="22" viewBox="0 0 18 22"><path d="M9 1 C4.5 1 1.5 4.5 1.5 8.5 C1.5 14 9 21 9 21 C9 21 16.5 14 16.5 8.5 C16.5 4.5 13.5 1 9 1 Z" fill="#fff"/><circle cx="9" cy="8.5" r="3" fill="#2f2e41"/></svg></span>
    <span>Mobile :<br>+61 0400 555 018</span>
  </div>
  <div class="abs contact-item" style="left:527px">
    <span class="dot"><svg width="20" height="16" viewBox="0 0 20 16"><rect x="1" y="1" width="18" height="14" rx="2" fill="#fff"/><path d="M1.5 2 L10 9 L18.5 2" fill="none" stroke="#2f2e41" stroke-width="1.8"/></svg></span>
    <span>Phone :<br>+61 7 5550 0142</span>
  </div>
  <div class="abs contact-item" style="left:928px;top:3195px">
    <span class="dot"><svg width="20" height="20" viewBox="0 0 20 20"><path d="M4 1 L7.5 1 L9 6 L6.5 7.5 C7.5 10 10 12.5 12.5 13.5 L14 11 L19 12.5 V16 C19 17.5 17.5 19 16 19 C8 18.5 1.5 12 1 4 C1 2.5 2.5 1 4 1 Z" fill="#fff"/></svg></span>
    <span>hello@plovencast.example</span>
  </div>

  <div class="abs footer"></div>
  <div class="abs brand center" style="top:3310px;font-size:46px">plovencast</div>
  <div class="abs social" style="left:482px">Share</div>
  <div class="abs social" style="left:543px">Follow</div>
  <div class="abs social" style="left:605px">Chat</div>
  <div class="abs social" style="left:665px">Post</div>
  <div class="abs footer-links center">Home<span>|</span>Our Services<span>|</span>Our Clients<span>|</span>Contact</div>
  <div class="abs copyright center">Copyrights © 2019.The Company Name. All rights reserved.Terms &amp; Services | Privacy Policy</div>

</div>
</body>
</html>
```